Poster Design Project for Over 50's Gym

We need a poster design to advertise our over 50's gym. We want to attract older adults who love enjoying their age, living life and having a bit of fun.
We would like to see a bright, fun, non-intimidating poster communicating how easy exercise can be and how great it can be for your health.
I would like the poster to include the following information.
Title:
Mackay's Over 50's Gym
Exercise with confidence
How old would you be if you didn't know your age?
Suitable exercise programmes for all medical conditions
Friendly and non-intimidating environment
Private health insurance rebates
University qualified exercise physiologists
Bright Pines Exercise Physiology Clinic
Exercise Physiologists Dorothy Linwell & Tobias Brandt
Suite 7, 238 Ridgeview Road, Mackay
www.tallowbrookfit.com.au
MON - FRI 8:30 am - 6:30 pm
I have photos available for use & Logo just unable to attach at moment****
Over 50 adult
Medical

```html
<!DOCTYPE html>
<html lang="en">
<head>
<meta charset="utf-8">
<title>Mackay's Over 50's Gym – Poster</title>
<link rel="stylesheet" href="https://fonts.googleapis.com/css2?family=Roboto+Condensed:wght@400;700&family=PT+Sans:wght@400;700&display=swap">
<style>
  :root {
    --navy: #213a73;
    --navy-deep: #1b3166;
    --yellow: #f8b52f;
    --orange: #f26a21;
    --white: #ffffff;
    --ink: #1d1d1d;
    --grey-text: #5d6470;
    --photo-light: #e9e6e2;
    --photo-dark: #8b8f95;
  }
  html, body { margin: 0; padding: 0; overflow: hidden; background: #ffffff; }
  .poster {
    position: relative;
    width: 900px;
    height: 1200px;
    overflow: hidden;
    font-family: "PT Sans", Arial, sans-serif;
    background: var(--white);
  }
  .backdrop { position: absolute; inset: 0; }

  .brand {
    position: absolute; top: 40px; left: 0; width: 900px;
    display: flex; justify-content: center; align-items: center; gap: 16px;
  }
  .brand-dot { width: 46px; height: 46px; border-radius: 50%; background: var(--orange); flex: none; }
  .brand-name {
    font-family: "PT Sans", Arial, sans-serif; font-weight: 700;
    color: var(--navy); font-size: 38px; line-height: 1.05;
  }
  .brand-name span { display: block; }

  .address {
    position: absolute; left: 330px; top: 162px;
    font-size: 20px; color: var(--ink); line-height: 1.35;
  }
  .address .web { color: var(--navy); font-weight: 700; letter-spacing: 1px; }

  .headline {
    position: absolute; left: 0; width: 900px; top: 300px; margin: 0;
    text-align: center; font-family: "Roboto Condensed", Arial, sans-serif;
    font-weight: 700; font-size: 72px; color: var(--yellow); letter-spacing: 0.5px;
  }
  .question {
    position: absolute; left: 60px; top: 424px; margin: 0;
    font-family: "Roboto Condensed", Arial, sans-serif; font-weight: 700;
    font-size: 28px; color: var(--white);
  }
  .benefits { position: absolute; left: 62px; top: 480px; margin: 0; padding: 0; list-style: none; }
  .benefits li {
    display: flex; align-items: center; gap: 12px;
    color: var(--white); font-size: 18px; height: 29px;
  }
  .benefits li::before {
    content: ""; width: 17px; height: 17px; border-radius: 50%;
    background: radial-gradient(circle at 35% 30%, #cfe4ff 0%, #5f93d8 45%, #2a5aa8 100%);
    box-shadow: 0 0 0 2px rgba(255,255,255,0.6);
  }
  .tagline {
    position: absolute; right: 60px; top: 546px; margin: 0; text-align: right;
    font-family: "Roboto Condensed", Arial, sans-serif; font-weight: 700;
    font-size: 50px; line-height: 1.1; color: var(--white);
    text-shadow: 2px 3px 4px rgba(0,0,0,0.35);
  }

  .hours {
    position: absolute; left: 66px; top: 682px; width: 160px; height: 160px;
    border-radius: 50%; background: #e9e9ea; border: 6px solid var(--orange);
    box-shadow: 0 0 0 6px var(--white);
    display: flex; flex-direction: column; align-items: center; justify-content: center;
    font-family: "PT Sans", Arial, sans-serif; color: var(--ink); text-align: center;
  }
  .hours .days { font-size: 30px; line-height: 1.1; }
  .hours .time { font-size: 22px; font-weight: 700; line-height: 1.2; }

  .call {
    position: absolute; left: 94px; top: 925px; margin: 0;
    font-size: 24px; color: var(--ink);
  }
  .call strong { font-size: 34px; font-weight: 700; margin-left: 6px; }

  .team {
    position: absolute; left: 55px; top: 984px; width: 343px; height: 189px;
    background: var(--navy); border-radius: 12px; box-sizing: border-box; padding: 10px 10px 0;
  }
  .team h2 {
    margin: 0; text-align: center; color: var(--yellow);
    font-family: "PT Sans", Arial, sans-serif; font-weight: 700; font-size: 21px;
  }
  .team-members { display: flex; gap: 14px; margin-top: 4px; }
  .member { flex: 1; text-align: center; }
  .member-name { color: var(--white); font-size: 13px; height: 18px; line-height: 18px; }
  .member-photo {
    height: 116px; border: 2px solid var(--white);
    background: linear-gradient(160deg, #c9c3bb 0%, #7d7a78 60%, #3d3f48 100%);
  }

  .hero-photo { position: absolute; left: 420px; top: 672px; width: 480px; height: 528px; }
</style>
</head>
<body>
<main class="poster">
  <svg class="backdrop" width="900" height="1200" viewBox="0 0 900 1200" aria-hidden="true">
    <rect x="0" y="560" width="900" height="640" fill="var(--yellow)"/>
    <path d="M0,150 C300,215 600,280 900,245 L900,1200 L420,1200 L420,906 C300,760 140,660 0,632 Z" fill="var(--navy)"/>
    <path d="M0,118 C300,190 600,262 900,226" fill="none" stroke="var(--yellow)" stroke-width="14"/>
    <path d="M0,134 C300,204 600,274 900,238" fill="none" stroke="var(--orange)" stroke-width="10"/>
    <path d="M0,600 C150,630 300,720 420,870" fill="none" stroke="var(--orange)" stroke-width="10"/>
    <path d="M0,585 C160,615 320,710 432,856" fill="none" stroke="var(--white)" stroke-width="5"/>
  </svg>

  <header class="brand">
    <span class="brand-dot"></span>
    <div class="brand-name"><span>Bright Pines</span><span>Exercise Physiology Clinic</span></div>
  </header>
  <div class="address">
    <div>Suite 7, 238 Ridgeview Road Mackay Q 4740</div>
    <div class="web">www.tallowbrookfit.com.au</div>
  </div>

  <h1 class="headline">Mackay's Over 50's Gym</h1>
  <p class="question">How old would you be if you didn't know your age?</p>
  <ul class="benefits">
    <li>Suitable exercise programmes for all medical conditions</li>
    <li>Friendly and non-intimidating environment</li>
    <li>Private health insurance rebates</li>
    <li>University qualified exercise physiologists</li>
  </ul>
  <p class="tagline">Exercise<br>with confidence</p>

  <div class="hours">
    <span class="days">MON - FRI</span>
    <span class="time">8:30 am to<br>6:30 pm</span>
  </div>

  <p class="call">Call Us: <strong>4960 3158</strong></p>

  <section class="team">
    <h2>EXERCISE PHYSIOLOGISTS</h2>
    <div class="team-members">
      <div class="member">
        <div class="member-name">Dorothy Linwell</div>
        <div class="member-photo" role="img" aria-label="Photo of exercise physiologist Dorothy Linwell in the gym"></div>
      </div>
      <div class="member">
        <div class="member-name">Tobias Brandt</div>
        <div class="member-photo" role="img" aria-label="Photo of exercise physiologist Tobias Brandt in the gym"></div>
      </div>
    </div>
  </section>

  <svg class="hero-photo" width="480" height="528" viewBox="0 0 480 528" role="img" aria-label="Photo of a smiling older woman in a white polo shirt at the gym">
    <defs>
      <linearGradient id="heroTone" x1="0" y1="0" x2="1" y2="1">
        <stop offset="0" stop-color="#3a3a3f"/>
        <stop offset="0.45" stop-color="var(--photo-dark)"/>
        <stop offset="1" stop-color="var(--photo-light)"/>
      </linearGradient>
    </defs>
    <path d="M12,528 V140 Q12,16 140,16 H480 V528 Z" fill="url(#heroTone)" stroke="var(--orange)" stroke-width="16"/>
    <path d="M12,528 V140 Q12,16 140,16 H480" fill="none" stroke="var(--white)" stroke-width="6"/>
  </svg>
</main>
</body>
</html>
```